Logistics Website Design

See website https://tqfreightglobal.com for theme and color details. Need the site to be re-done and reflect some of the designs shown in this list here: https://pixelvane.com/tags/logistics-company-website

Target Market(s)

Logistics & Transportation

Industry/Entity Type

Logistics and Supply Chain

Coding

Number of Pages Required

5+ page

Requirements
Must have
• Colors must match theme of logo. Looking for a sleek, interactive design.

```html
<!DOCTYPE html>
<html lang="en">
<head>
<meta charset="utf-8">
<title>TQ Freight Global — Delivering Strength in Every Mile</title>
<link href="https://fonts.googleapis.com/css2?family=Barlow+Condensed:wght@500;600;700&family=Inter:wght@400;500;600&family=Orbitron:wght@500&display=swap" rel="stylesheet">
<style>
:root{
  --bg:#140603;
  --bg-2:#1d0a05;
  --panel:#26110a;
  --panel-2:#341509;
  --brown:#4a1f0e;
  --accent:#ee6b3b;
  --accent-2:#c9501f;
  --accent-soft:#f2a57e;
  --text:#f4ece8;
  --muted:#c9b6ad;
  --line:#5a2c1a;
}
*{box-sizing:border-box;margin:0;padding:0}
html,body{width:1200px;height:5133px;overflow:hidden}
body{background:var(--bg);color:var(--text);font-family:"Inter",sans-serif;position:relative}
.abs{position:absolute}
.head{font-family:"Barlow Condensed",sans-serif;font-weight:700;text-transform:uppercase;letter-spacing:.5px;line-height:1}
.tag{font-family:"Orbitron",sans-serif;font-size:11px;letter-spacing:3px;color:var(--accent);text-transform:uppercase}
.hl{background:#fff;color:#1a0904;padding:0 8px;border-radius:4px;display:inline-block}
.btn{display:inline-flex;align-items:center;gap:12px;background:linear-gradient(90deg,var(--accent-2),var(--accent));color:#fff;font-family:"Barlow Condensed",sans-serif;font-weight:600;font-size:14px;text-transform:uppercase;border-radius:22px;padding:0 6px 0 18px;height:40px}
.btn .arr{width:30px;height:30px;border-radius:50%;background:#2a0f06;display:flex;align-items:center;justify-content:center}
.img{border-radius:4px}
p{line-height:1.55}

/* header / hero */
.hero{left:0;top:0;width:1200px;height:690px;background:linear-gradient(180deg,#3d1a0c 0%,#6a2e15 45%,#2b1008 100%)}
.hero-photo{left:600px;top:60px;width:600px;height:540px;background:radial-gradient(ellipse at 55% 45%,#d8d6d8 0%,#8d7a72 35%,#5a2a16 70%,transparent 100%)}
.chevron{left:0;top:560px;width:1200px;height:140px}
.logo{display:flex;align-items:center;gap:10px}
.logo .dot{width:44px;height:44px;border-radius:50%;background:var(--accent)}
.logo span{font-family:"Barlow Condensed",sans-serif;font-weight:700;font-size:22px;text-transform:uppercase;color:var(--text)}
.nav{left:294px;top:34px;display:flex;gap:44px;font-family:"Barlow Condensed",sans-serif;font-weight:600;font-size:14px;text-transform:uppercase}
.nav a{color:var(--text);text-decoration:none}
.stats{top:730px;left:140px;width:920px;display:flex}
.stat{flex:1;text-align:center;border-left:1px solid var(--line);padding:8px 0}
.stat:first-child{border-left:none}
.stat b{display:block;font-family:"Barlow Condensed",sans-serif;font-weight:600;font-size:56px}
.stat small{font-family:"Barlow Condensed",sans-serif;font-size:14px;color:var(--accent);text-transform:uppercase}

/* services */
.services-bg{left:0;top:1480px;width:1200px;height:620px;background:linear-gradient(180deg,#4a1d0c,#2a0f06 70%,#1a0805)}
.card{width:256px;height:410px;background:var(--panel);border-radius:4px;overflow:hidden;text-align:center}
.card.active{background:linear-gradient(180deg,#3a170a,#6a2c12);border:1px solid var(--accent-2)}
.card .ph{height:190px}
.card h3{font-family:"Barlow Condensed",sans-serif;font-weight:600;font-size:21px;text-transform:uppercase;line-height:1.05;margin:8px 0 10px}
.card p{font-size:11px;color:var(--muted);padding:0 24px}
.card .btn{height:32px;font-size:12px;margin-top:18px}
.card .btn .arr{width:22px;height:22px}

/* why */
.why-item h4{font-family:"Barlow Condensed",sans-serif;font-weight:600;font-size:24px;text-transform:uppercase;line-height:1.1}
.why-item p{font-size:11.5px;color:var(--muted);margin-top:8px}
.ring{width:96px;height:96px;border-radius:50%;border:3px solid var(--accent);display:flex;align-items:center;justify-content:center;background:#220c05}

/* industries */
.ind{width:194px;height:166px;background:#1c0905;border:1px solid #3a1a0e;border-radius:4px;text-align:center;padding-top:28px}
.ind .ico{width:52px;height:52px;margin:0 auto 22px;border-radius:6px;background:linear-gradient(180deg,var(--accent),var(--accent-2));display:flex;align-items:center;justify-content:center}
.ind h5{font-family:"Barlow Condensed",sans-serif;font-weight:600;font-size:16px;text-transform:uppercase}
.ind.active{height:212px;background:linear-gradient(180deg,#2a0f06,#4a1d0c);border-color:var(--accent-2)}

/* testimonials */
.tcard{width:324px;height:304px;border:1px solid #4a2414;border-radius:6px;background:#190804;padding:26px 34px}
.tcard p{font-size:12px;color:var(--muted);margin-top:26px}
.who{display:flex;align-items:center;gap:10px;margin-top:18px}
.who .av{width:38px;height:38px;border-radius:50%;background:#7a5a4a}
.who b{font-size:13px;font-weight:600}
.stars{color:var(--accent);font-size:11px;letter-spacing:2px}

/* form */
.field{background:#2a1109;border:1px solid #5a2c1a;border-radius:2px;font-size:12px;color:var(--text);display:flex;align-items:center;gap:10px;padding:0 18px;height:52px}

/* footer */
.foot-nav a{display:flex;align-items:center;gap:16px;font-family:"Barlow Condensed",sans-serif;font-weight:600;font-size:22px;text-transform:uppercase;color:var(--text);text-decoration:none;height:52px;border-bottom:1px solid #3a1a0e}
.foot-svc li{list-style:none;font-family:"Barlow Condensed",sans-serif;font-size:21px;text-transform:uppercase;height:36px}
.social{width:34px;height:34px;border-radius:50%;border:2px solid var(--accent)}
</style>
</head>
<body>

<!-- HERO -->
<section class="abs hero">
  <div class="abs hero-photo" role="img" aria-label="White semi truck with dry van trailer driving on a desert highway at sunset"></div>
</section>
<svg class="abs chevron" viewBox="0 0 1200 140" preserveAspectRatio="none"><path d="M0 0 L600 110 L1200 0 L1200 140 L0 140Z" fill="var(--bg)"/></svg>

<header>
  <div class="abs logo" style="left:96px;top:44px"><div class="dot"></div><span>TQ Freight Global</span></div>
  <nav class="abs nav">
    <a href="#">Home</a><a href="#">Services</a><a href="#">Industries</a><a href="#">About Us</a><a href="#">Contact Us</a>
  </nav>
  <div class="abs btn" style="left:940px;top:24px">Request a Quote <span class="arr"><svg width="12" height="12" viewBox="0 0 12 12"><path d="M2 10 L10 2 M4 2 H10 V8" stroke="#fff" stroke-width="1.6" fill="none"/></svg></span></div>
</header>

<div class="abs head" style="left:96px;top:206px;font-size:64px">
  <span class="hl">Delivering</span> Strength<br><span style="display:inline-block;margin-top:10px;margin-left:8px">In Every Mile</span>
</div>
<div class="abs" style="left:104px;top:362px;width:500px;border-left:2px solid var(--accent);padding-left:14px;font-size:15px;color:var(--muted)">
  <p>We deliver a comprehensive range of open-deck and specialized transportation services—including flatbed, step deck, heavy haul, and over-dimensional freight solutions.</p>
</div>
<div class="abs btn" style="left:102px;top:462px">Request a Quote <span class="arr"><svg width="12" height="12" viewBox="0 0 12 12"><path d="M2 10 L10 2 M4 2 H10 V8" stroke="#fff" stroke-width="1.6" fill="none"/></svg></span></div>
<div class="abs btn" style="left:296px;top:462px;padding:0 18px 0 6px"><span class="arr"><svg width="14" height="14" viewBox="0 0 14 14"><path d="M3 1 L6 4 L4.5 6 Q7 9.5 8 9.5 L10 8 L13 11 L11 13 Q5 13 1 3Z" fill="#fff"/></svg></span> Call Us Now</div>

<!-- STATS -->
<div class="abs stats">
  <div class="stat"><b>250</b><small>Lorem ipsum dolor sit</small></div>
  <div class="stat"><b>30K+</b><small>Lorem ipsum dolor sit</small></div>
  <div class="stat"><b>260</b><small>Lorem ipsum dolor sit</small></div>
  <div class="stat"><b>180</b><small>Lorem ipsum dolor sit</small></div>
</div>

<!-- ABOUT -->
<section>
  <div class="abs img" style="left:112px;top:1020px;width:454px;height:366px;background:linear-gradient(135deg,#c9b3a6,#7d6358 55%,#3a2a24)" role="img" aria-label="White box truck in motion on a highway"></div>
  <div class="abs" style="left:528px;top:1164px;width:64px;height:64px;border-radius:50%;background:#1a0804;border:3px solid var(--accent);display:flex;align-items:center;justify-content:center"><svg width="22" height="22" viewBox="0 0 22 22"><circle cx="11" cy="11" r="10" fill="var(--accent)"/><path d="M8 6 L16 11 L8 16Z" fill="#1a0804"/></svg></div>
  <div class="abs tag" style="left:640px;top:1012px">About Company</div>
  <div class="abs head" style="left:638px;top:1040px;font-size:56px">Keeping Your Supply<br><span class="hl" style="margin-top:8px">Chain Moving</span></div>
  <div class="abs" style="left:636px;top:1188px;width:500px;font-size:15px;color:var(--muted)">
    <p>We deliver a comprehensive range of open-deck and specialized transportation services—including flatbed, step deck, heavy haul, and over-dimensional freight solutions. Backed by years of experience, a trusted nationwide carrier network, and a strong safety-first culture, we provide reliable, adaptable logistics support built around the unique requirements of every load.</p>
  </div>
  <div class="abs btn" style="left:632px;top:1366px">Learn More <span class="arr"><svg width="12" height="12" viewBox="0 0 12 12"><path d="M2 10 L10 2 M4 2 H10 V8" stroke="#fff" stroke-width="1.6" fill="none"/></svg></span></div>
</section>

<!-- SERVICES -->
<section>
  <div class="abs services-bg"></div>
  <div class="abs tag" style="left:0;width:1200px;text-align:center;top:1520px">What We Do</div>
  <div class="abs head" style="left:0;width:1200px;text-align:center;top:1552px;font-size:56px">Our <span class="hl">Services</span></div>

  <div class="abs card" style="left:60px;top:1666px">
    <div class="ph" role="img" aria-label="Semi truck on a flatbed route" style="background:linear-gradient(180deg,#6e7c88,#3d3a3a)"></div>
    <svg width="28" height="28" viewBox="0 0 28 28" style="margin-top:14px"><rect x="6" y="4" width="16" height="14" rx="2" fill="var(--accent)"/><rect x="4" y="18" width="20" height="4" fill="var(--accent)"/></svg>
    <h3>Flatbed<br>Transportation</h3>
    <p>From routine shipments to oversized and heavy-haul loads, we handle freight requiring proper</p>
    <div class="btn">Learn More <span class="arr"><svg width="10" height="10" viewBox="0 0 12 12"><path d="M2 10 L10 2 M4 2 H10 V8" stroke="#fff" stroke-width="1.6" fill="none"/></svg></span></div>
  </div>
  <div class="abs card active" style="left:334px;top:1666px">
    <div class="ph" role="img" aria-label="Red step deck trailer parked by a warehouse" style="background:linear-gradient(180deg,#9aa7b4,#8a4a36)"></div>
    <svg width="28" height="28" viewBox="0 0 28 28" style="margin-top:14px"><rect x="4" y="10" width="20" height="10" rx="2" fill="var(--accent)"/><path d="M8 10 L14 4 L20 10" stroke="var(--accent)" stroke-width="2" fill="none"/></svg>
    <h3>Step Deck<br>Transportation</h3>
    <p>From routine shipments to oversized and heavy-haul loads, we handle freight requiring proper</p>
    <div class="btn">Learn More <span class="arr"><svg width="10" height="10" viewBox="0 0 12 12"><path d="M2 10 L10 2 M4 2 H10 V8" stroke="#fff" stroke-width="1.6" fill="none"/></svg></span></div>
  </div>
  <div class="abs card" style="left:608px;top:1666px">
    <div class="ph" role="img" aria-label="Dry van trailers on a highway at dusk" style="background:linear-gradient(180deg,#c27a4a,#3a2a2a)"></div>
    <svg width="28" height="28" viewBox="0 0 28 28" style="margin-top:14px"><rect x="3" y="8" width="15" height="11" fill="var(--accent)"/><rect x="18" y="11" width="7" height="8" fill="var(--accent)"/><circle cx="8" cy="22" r="2.5" fill="var(--accent)"/><circle cx="21" cy="22" r="2.5" fill="var(--accent)"/></svg>
    <h3>Dry Van<br>Transportation</h3>
    <p>From routine shipments to oversized and heavy-haul loads, we handle freight requiring proper</p>
    <div class="btn">Learn More <span class="arr"><svg width="10" height="10" viewBox="0 0 12 12"><path d="M2 10 L10 2 M4 2 H10 V8" stroke="#fff" stroke-width="1.6" fill="none"/></svg></span></div>
  </div>
  <div class="abs card" style="left:882px;top:1666px">
    <div class="ph" role="img" aria-label="Heavy haul truck carrying a yellow machine" style="background:linear-gradient(180deg,#8fa0b0,#6a5a3a)"></div>
    <svg width="28" height="28" viewBox="0 0 28 28" style="margin-top:14px"><rect x="3" y="10" width="14" height="9" fill="var(--accent)"/><rect x="17" y="13" width="8" height="6" fill="var(--accent)"/><circle cx="8" cy="22" r="2.5" fill="var(--accent)"/><circle cx="21" cy="22" r="2.5" fill="var(--accent)"/></svg>
    <h3>Heavy Haul<br>Transportation</h3>
    <p>From routine shipments to oversized and heavy-haul loads, we handle freight requiring proper</p>
    <div class="btn">Learn More <span class="arr"><svg width="10" height="10" viewBox="0 0 12 12"><path d="M2 10 L10 2 M4 2 H10 V8" stroke="#fff" stroke-width="1.6" fill="none"/></svg></span></div>
  </div>
</section>

<!-- WHY CHOOSE US -->
<section>
  <svg class="abs" style="left:0;top:2100px" width="1200" height="130" viewBox="0 0 1200 130"><path d="M0 0 L600 80 L1200 0 L1200 130 L0 130Z" fill="var(--bg)"/><line x1="600" y1="80" x2="600" y2="150" stroke="var(--line)"/></svg>
  <div class="abs tag" style="left:0;width:1200px;text-align:center;top:2284px">Why We Are</div>
  <div class="abs head" style="left:0;width:1200px;text-align:center;top:2316px;font-size:56px">Why <span class="hl">Choose Us</span></div>

  <svg class="abs" style="left:0;top:2400px" width="1200" height="420" viewBox="0 0 1200 420">
    <g stroke="var(--accent)" stroke-width="3" fill="none">
      <path d="M154 96 V150 Q154 160 164 160 H230 Q240 160 240 170 V190 H424"/>
      <path d="M1056 96 V150 Q1056 160 1046 160 H970 Q960 160 960 170 V190 H784"/>
      <path d="M424 230 H240 Q230 230 230 240 V230 H164 Q154 230 154 240 V254"/>
      <path d="M784 230 H960 V230 H1046 Q1056 230 1056 240 V254"/>
    </g>
    <circle cx="154" cy="160" r="6" fill="var(--bg)" stroke="var(--accent)" stroke-width="2"/>
    <circle cx="1056" cy="160" r="6" fill="var(--bg)" stroke="var(--accent)" stroke-width="2"/>
    <circle cx="154" cy="230" r="6" fill="var(--bg)" stroke="var(--accent)" stroke-width="2"/>
    <circle cx="1056" cy="230" r="6" fill="var(--bg)" stroke="var(--accent)" stroke-width="2"/>
  </svg>

  <div class="abs" style="left:452px;top:2466px;width:300px;height:300px;border-radius:50%;background:radial-gradient(circle,#4a1d0c,#2a0f06);border:6px solid #6a2c12;display:flex;align-items:center;justify-content:center;text-align:center">
    <div>
      <div style="width:70px;height:70px;border-radius:50%;background:var(--accent);margin:0 auto 16px"></div>
      <div class="head" style="font-size:36px;color:var(--text)">TQ Freight Global</div>
    </div>
  </div>

  <div class="abs ring" style="left:106px;top:2402px"><svg width="40" height="40" viewBox="0 0 40 40" fill="none" stroke="#fff" stroke-width="2.5"><circle cx="18" cy="20" r="14"/><path d="M18 12 V20 H24"/><circle cx="30" cy="28" r="7" fill="var(--accent)" stroke="none"/><path d="M27 28 L29.5 30.5 L33.5 26"/></svg></div>
  <div class="abs why-item" style="left:218px;top:2420px;width:240px"><h4>Reliable &amp;<br>On-Time Delivery</h4><p>We ensure every shipment reaches its destination safely and on schedule.</p></div>

  <div class="abs ring" style="left:1008px;top:2402px"><svg width="40" height="40" viewBox="0 0 40 40" fill="none" stroke="#fff" stroke-width="2.5"><circle cx="20" cy="13" r="5"/><circle cx="9" cy="17" r="4"/><circle cx="31" cy="17" r="4"/><path d="M11 32 Q11 22 20 22 Q29 22 29 32Z M3 32 Q3 25 9 25 M37 32 Q37 25 31 25"/></svg></div>
  <div class="abs why-item" style="left:730px;top:2420px;width:260px;text-align:right"><h4>Experienced &amp;<br>Professional Team</h4><p>Our logistics experts bring years of industry experience to every shipment.</p></div>

  <div class="abs ring" style="left:106px;top:2652px"><svg width="40" height="40" viewBox="0 0 40 40" fill="none" stroke="#fff" stroke-width="2.5"><path d="M12 22 Q4 13 12 6 Q20 13 12 22Z"/><circle cx="12" cy="12" r="2.5"/><path d="M12 24 Q12 32 22 30 Q34 28 30 34"/><circle cx="30" cy="34" r="2"/></svg></div>
  <div class="abs why-item" style="left:218px;top:2676px;width:260px"><h4>Global Network<br>&amp; Reach</h4><p>With a strong worldwide logistics network, we connect businesses across borders.</p></div>

  <div class="abs ring" style="left:1008px;top:2652px"><svg width="40" height="40" viewBox="0 0 40 40" fill="none" stroke="#fff" stroke-width="2.5"><rect x="6" y="10" width="18" height="16"/><path d="M24 16 H31 L35 21 V26 H24Z"/><circle cx="12" cy="29" r="3"/><circle cx="29" cy="29" r="3"/><path d="M2 15 H10 M2 20 H8"/></svg></div>
  <div class="abs why-item" style="left:720px;top:2676px;width:270px;text-align:right"><h4>Customized<br>Logistics Solutions</h4><p>We tailor our services to match your unique shipping and business needs.</p></div>
</section>

<!-- INDUSTRIES -->
<section>
  <div class="abs" style="left:0;top:2930px;width:1200px;height:500px;background:linear-gradient(180deg,var(--bg) 0%,#2f1208 60%,var(--bg) 100%)"></div>
  <div class="abs tag" style="left:0;width:1200px;text-align:center;top:2948px">Who We Serve</div>
  <div class="abs head" style="left:0;width:1200px;text-align:center;top:2980px;font-size:56px">Industries <span class="hl">We Serve</span></div>

  <div class="abs ind" style="left:92px;top:3120px"><div class="ico"><svg width="26" height="26" viewBox="0 0 26 26" fill="#fff"><rect x="4" y="12" width="18" height="10" rx="2"/><circle cx="10" cy="8" r="4"/><circle cx="17" cy="8" r="3"/></svg></div><h5>Food &amp; Beverage</h5></div>
  <div class="abs ind active" style="left:304px;top:3106px"><div class="ico"><svg width="26" height="26" viewBox="0 0 26 26" fill="none" stroke="#fff" stroke-width="2.2"><path d="M2 4 H6 L9 17 H21 L23 8 H8"/><circle cx="10" cy="21" r="1.8" fill="#fff"/><circle cx="19" cy="21" r="1.8" fill="#fff"/></svg></div><h5>E-Commerce &amp; Retail</h5>
    <p style="font-size:9px;color:var(--muted);padding:6px 20px 0;line-height:1.4">Lorem ipsum dolor sit amet, consectetur adipiscing elit</p>
    <div style="width:26px;height:26px;border-radius:50%;background:var(--accent);margin:14px 0 0 20px;display:flex;align-items:center;justify-content:center"><svg width="10" height="10" viewBox="0 0 12 12"><path d="M2 10 L10 2 M4 2 H10 V8" stroke="#fff" stroke-width="1.8" fill="none"/></svg></div>
  </div>
  <div class="abs ind" style="left:516px;top:3120px"><div class="ico"><svg width="26" height="26" viewBox="0 0 26 26" fill="#fff"><path d="M3 22 V10 L9 14 V10 L15 14 V6 H21 V22Z"/></svg></div><h5>Manufacturing</h5></div>
  <div class="abs ind" style="left:728px;top:3120px"><div class="ico"><svg width="26" height="26" viewBox="0 0 26 26" fill="#fff"><rect x="5" y="4" width="16" height="18" rx="2"/><path d="M11 9 H15 V12 H18 V16 H15 V19 H11 V16 H8 V12 H11Z" fill="var(--accent-2)"/></svg></div><h5>Pharma &amp; Healthcare</h5></div>
  <div class="abs ind" style="left:938px;top:3120px"><div class="ico"><svg width="26" height="26" viewBox="0 0 26 26" fill="#fff"><path d="M3 10 L13 4 L23 10Z"/><rect x="5" y="11" width="3" height="9"/><rect x="11.5" y="11" width="3" height="9"/><rect x="18" y="11" width="3" height="9"/><rect x="3" y="20" width="20" height="3"/></svg></div><h5>Government</h5></div>
</section>

<!-- TESTIMONIALS -->
<section>
  <div class="abs tag" style="left:118px;top:3546px">Testimonials</div>
  <div class="abs head" style="left:112px;top:3576px;font-size:58px;line-height:1.08">See What<br>Our Customer<br><span class="hl">Are Saying</span></div>
  <div class="abs" style="left:114px;top:3770px;width:300px;font-size:12px;color:var(--muted)"><p>Lorem ipsum dolor sit amet, consectetur adipiscing elit, sed do eiusmod tempor incididunt</p></div>
  <div class="abs" style="left:124px;top:3852px;width:30px;height:30px;border-radius:50%;background:var(--accent);display:flex;align-items:center;justify-content:center"><svg width="14" height="14" viewBox="0 0 14 14"><path d="M12 7 H2 M6 3 L2 7 L6 11" stroke="#1a0804" stroke-width="2" fill="none"/></svg></div>
  <div class="abs" style="left:172px;top:3852px;width:30px;height:30px;border-radius:50%;background:var(--accent);display:flex;align-items:center;justify-content:center"><svg width="14" height="14" viewBox="0 0 14 14"><path d="M2 7 H12 M8 3 L12 7 L8 11" stroke="#1a0804" stroke-width="2" fill="none"/></svg></div>

  <div class="abs tcard" style="left:460px;top:3542px">
    <svg width="56" height="30" viewBox="0 0 56 30" fill="#5a3a2e"><path d="M0 0 H22 V18 L14 30 H4 L10 18 H0Z M30 0 H52 V18 L44 30 H34 L40 18 H30Z"/></svg>
    <p>"Lorem ipsum dolor sit amet, consectetur adipiscing elit, sed do eiusmod tempor incididunt ut labore et dolore magna aliqua. Quis ipsum suspendisse ultrices gravida. Risus commodo viverra maecenas accumsan lacus vel facilisis"</p>
    <div class="who"><div class="av" role="img" aria-label="Customer portrait"></div><div><b>Sam Rowe</b><div class="stars">★★★★★</div></div></div>
  </div>
  <div class="abs tcard" style="left:806px;top:3542px">
    <svg width="56" height="30" viewBox="0 0 56 30" fill="#5a3a2e"><path d="M0 0 H22 V18 L14 30 H4 L10 18 H0Z M30 0 H52 V18 L44 30 H34 L40 18 H30Z"/></svg>
    <p>"Lorem ipsum dolor sit amet, consectetur adipiscing elit, sed do eiusmod tempor incididunt ut labore et dolore magna aliqua. Quis ipsum suspendisse ultrices gravida. Risus commodo viverra maecenas accumsan lacus vel facilisis"</p>
    <div class="who"><div class="av" role="img" aria-label="Customer portrait"></div><div><b>Sam Rowe</b><div class="stars">★★★★★</div></div></div>
  </div>
</section>

<!-- REQUEST A QUOTE -->
<section>
  <div class="abs" style="left:0;top:3960px;width:1200px;height:670px;background:linear-gradient(180deg,var(--bg) 0%,#5a2410 30%,#2e1108 75%,#1e0a05 100%)"></div>
  <div class="abs" style="left:0;top:4090px;width:620px;height:540px;background:radial-gradient(ellipse at 50% 55%,#d6d2d0 0%,#8a7a74 30%,#3a1a0e 70%,transparent 100%)" role="img" aria-label="White cab-over truck with trailer on a road at night"></div>
  <div class="abs tag" style="left:0;width:1200px;text-align:center;top:4008px">Contact Us</div>
  <div class="abs head" style="left:0;width:1200px;text-align:center;top:4036px;font-size:56px">Request a <span class="hl">Quote</span></div>

  <div class="abs field" style="left:618px;top:4174px;width:230px">
    <svg width="12" height="12" viewBox="0 0 12 12" fill="#ddd"><circle cx="6" cy="3.5" r="3"/><path d="M0 12 Q0 7 6 7 Q12 7 12 12Z"/></svg>First Name</div>
  <div class="abs field" style="left:858px;top:4174px;width:230px">
    <svg width="12" height="12" viewBox="0 0 12 12" fill="#ddd"><circle cx="6" cy="3.5" r="3"/><path d="M0 12 Q0 7 6 7 Q12 7 12 12Z"/></svg>Last Name</div>
  <div class="abs field" style="left:618px;top:4236px;width:230px">
    <svg width="14" height="10" viewBox="0 0 14 10"><rect width="14" height="10" rx="1" fill="#ddd"/><path d="M0 0 L7 6 L14 0" stroke="#2a1109" fill="none"/></svg>Email address</div>
  <div class="abs field" style="left:858px;top:4236px;width:230px">
    <svg width="12" height="12" viewBox="0 0 14 14"><path d="M3 1 L6 4 L4.5 6 Q7 9.5 8 9.5 L10 8 L13 11 L11 13 Q5 13 1 3Z" fill="#ddd"/></svg>Phone</div>
  <div class="abs field" style="left:618px;top:4298px;width:470px;height:112px;align-items:flex-start;padding-top:16px">
    <svg width="12" height="12" viewBox="0 0 12 12" fill="#ddd"><path d="M1 1 H11 V8 H5 L2 11 V8 H1Z"/></svg>Message</div>
  <div class="abs btn" style="left:616px;top:4434px">Send Message <span class="arr"><svg width="12" height="12" viewBox="0 0 12 12"><path d="M2 10 L10 2 M4 2 H10 V8" stroke="#fff" stroke-width="1.6" fill="none"/></svg></span></div>
</section>

<!-- FOOTER -->
<footer>
  <div class="abs" style="left:0;top:4630px;width:1200px;height:503px;background:linear-gradient(180deg,#2a0e06,#1a0704)"></div>
  <div class="abs" style="left:120px;top:4720px;width:152px;height:152px;border-radius:50%;background:#3a1609;border:4px solid var(--accent);display:flex;align-items:center;justify-content:center;text-align:center">
    <span class="head" style="font-size:22px">TQ Freight<br>Global</span>
  </div>
  <div class="abs" style="left:136px;top:4860px;display:flex;gap:14px">
    <div class="social"></div><div class="social"></div><div class="social"></div>
  </div>

  <nav class="abs foot-nav" style="left:372px;top:4700px;width:216px">
    <a href="#"><svg width="14" height="14" viewBox="0 0 14 14" fill="var(--accent)"><path d="M7 1 L13 7 H11 V13 H3 V7 H1Z"/></svg>Home</a>
    <a href="#"><svg width="14" height="14" viewBox="0 0 12 12" fill="var(--accent)"><circle cx="6" cy="3.5" r="3"/><path d="M0 12 Q0 7 6 7 Q12 7 12 12Z"/></svg>About</a>
    <a href="#"><svg width="14" height="14" viewBox="0 0 26 26" fill="var(--accent)"><path d="M3 22 V10 L9 14 V10 L15 14 V6 H21 V22Z"/></svg>Industries</a>
    <a href="#" style="border-bottom:none"><svg width="14" height="14" viewBox="0 0 14 14" fill="var(--accent)"><path d="M3 1 L6 4 L4.5 6 Q7 9.5 8 9.5 L10 8 L13 11 L11 13 Q5 13 1 3Z"/></svg>Contact Us</a>
  </nav>

  <div class="abs" style="left:810px;top:4700px;width:1px;height:170px;background:#3a1a0e"></div>
  <div class="abs head" style="left:642px;top:4696px;font-size:22px;font-weight:600">Services</div>
  <ul class="abs foot-svc" style="left:644px;top:4736px">
    <li><span style="color:var(--accent)">»</span> Flatbed</li>
    <li><span style="color:var(--accent)">»</span> Step Deck</li>
    <li><span style="color:var(--accent)">»</span> Dry Van</li>
    <li><span style="color:var(--accent)">»</span> Heavy Haul</li>
  </ul>

  <div class="abs head" style="left:870px;top:4696px;font-size:22px;font-weight:600">Newsletter Sign Up</div>
  <div class="abs field" style="left:868px;top:4746px;width:238px;height:38px;font-size:11px">
    <svg width="12" height="9" viewBox="0 0 14 10"><rect width="14" height="10" rx="1" fill="var(--accent)"/></svg>Email address</div>
  <div class="abs btn" style="left:868px;top:4794px;width:238px;height:36px;border-radius:2px;justify-content:space-between;padding-left:76px">Subscribe Now <span class="arr" style="width:24px;height:24px"><svg width="10" height="10" viewBox="0 0 12 12"><path d="M2 10 L10 2 M4 2 H10 V8" stroke="#fff" stroke-width="1.6" fill="none"/></svg></span></div>

  <div class="abs" style="left:24px;top:4990px;width:1152px;height:1px;background:#3a1a0e"></div>
  <div class="abs" style="left:0;width:1200px;text-align:center;top:5018px;font-size:12px;color:var(--muted)">© 2026. An independent agent of Crestline Haulage LLC.</div>
  <div class="abs" style="left:1062px;top:5012px;width:22px;height:22px;border-radius:50%;background:var(--accent)"></div>
  <div class="abs head" style="left:0;width:1200px;text-align:center;top:5056px;font-size:130px;color:#2e130a;letter-spacing:6px">TQ Freight Global</div>
</footer>

</body>
</html>
```